Philadelphia-based Nonprofit Needs Invitation Design for 11th Annual Cook-Off Fundraiser

Venture Hollow (VH) is a non-profit 501(c)(3) microenterprise development organization focused on growing businesses and jobs in our local communities. By connecting hundreds of entrepreneurs each year with access to capital, one-on-one technical assistance, business training and networking opportunities, Venture Hollow helps promising individuals to develop economic self-sufficiency and create job opportunities through business ownership.

The theme for our 11th annual Plate of Promise cook-off fundraiser, “Tastes from Around the World: Savor the Flavors,” reflects our commitment to fostering and celebrating the diverse network of entrepreneurs, business owners, and supporters that make VH’s work possible.

Plate of Promise is a chance for Venture Hollow to showcase the culinary talents of our entrepreneurs and business owners, while also hosting a fun-filled night with celebrity guest judges, delicious hors d'oeuvres and desserts, a silent auction, and an exciting cook-off contest.

We would like a double-sided, two-color folded invitation (fold size: 5" x 7"); a double-sided, two-color reply card (5” x 4”); a mailing envelope (A7 envelope, grayscale) and a reply envelope (A2 envelope, grayscale). For an example of the design that was on the cover of last year's invitation, see here: http://www.myventurehollow.example/sites/vh.brightquill.example/files/imagecache/250px_thumb/signature_images/VH_RiverBendSupper.png.

The final design should appeal to a broad range of potential attendees and be inviting and warm. While we send out a different invitation for each Plate of Promise fundraiser, we were very pleased with last year’s invitation (attached, “Plate of Promise Invitation_2011”) and would like an invitation design that is similar (for color scheme please refer to the web link in the above paragraph). A scanned copy of the reply card is also attached ("Plate of Promise Reply Cards 2011"). Finally a copy of the outer envelope is attached ("Plate of Promise Outer Envelope_2011").

Target Market(s)

Our target market includes: existing and past donors; local business owners; and entrepreneurs.

Industry/Entity Type

Non-Profit

Requirements
Must have
• - The main illustration on the invitation should be food-themed
- The invitation should include all of the copy in the attached word .doc ("Plate of Promise Invitation Copy_2013").
Should not have
• - Any designs, backgrounds or fonts that make the invitation difficult to read or understand

```html
<!DOCTYPE html>
<html lang="en">
<head>
<meta charset="utf-8">
<title>Plate of Promise 2013 – Reply Card</title>
<link rel="stylesheet" href="https://fonts.googleapis.com/css2?family=Parisienne&family=Open+Sans:wght@400;700&family=Montserrat:wght@600;700&display=swap">
<style>
  :root {
    --brick: #963a37;
    --paper: #ffffff;
    --ink: #111111;
    --script: "Parisienne", cursive;
    --body: "Open Sans", Arial, sans-serif;
    --display: "Montserrat", Arial, sans-serif;
  }
  * { box-sizing: border-box; margin: 0; padding: 0; }
  html, body { width: 1200px; height: 924px; overflow: hidden; background: var(--paper); }
  .card { position: relative; width: 1200px; height: 924px; background: var(--paper); color: var(--ink); font-family: var(--body); }

  .theme-panel { position: absolute; left: 0; top: 0; width: 548px; height: 838px; background: var(--brick); }
  .theme-title {
    position: absolute; left: 20px; top: 62px; width: 520px;
    font-family: var(--script); color: var(--paper); font-size: 38px; line-height: 1.2;
    text-align: center; transform: rotate(4deg);
  }
  .pot-art { position: absolute; left: 0; top: 215px; }
  .event-ribbon { position: absolute; left: 88px; top: 712px; }

  .brand-bar { position: absolute; left: 0; top: 838px; width: 548px; height: 86px; background: var(--paper); }
  .brand-name {
    position: absolute; left: 0; top: 0; width: 548px; height: 86px;
    display: flex; align-items: center; justify-content: center;
    font-family: var(--body); font-weight: 400; color: var(--brick);
    font-size: 26px; letter-spacing: .3px;
  }

  .reply-form { position: absolute; left: 585px; top: 0; width: 590px; }
  .welcome {
    position: absolute; left: 0; top: 14px; width: 580px; text-align: center;
    font-family: var(--script); font-weight: 400; font-size: 50px; line-height: 66px;
  }
  .tickets { position: absolute; left: 0; top: 180px; font-size: 26px; line-height: 38px; }
  .tickets h2, .ticket-type { font-size: 26px; font-weight: 700; }
  .ticket-group + .ticket-group { margin-top: 28px; }
  .blank { display: inline-block; border-bottom: 1.5px solid var(--ink); height: 24px; vertical-align: baseline; }
  .contact { position: absolute; left: 0; top: 436px; font-size: 26px; line-height: 39px; }
  .guests-note { position: absolute; left: 0; top: 616px; width: 515px; font-size: 26px; line-height: 38px; }
  .guest-line { position: absolute; left: 0; width: 576px; border-bottom: 1.5px solid var(--ink); }

  .deadline {
    position: absolute; left: 548px; top: 838px; width: 652px; height: 86px;
    background: var(--brick); color: var(--paper);
    font-family: var(--display); font-weight: 700; font-size: 38px;
    display: flex; align-items: center; justify-content: center; letter-spacing: .3px;
  }
  .deadline sup { font-size: 22px; vertical-align: 14px; }
</style>
</head>
<body>
<main class="card">
  <section class="theme-panel">
    <p class="theme-title">Tastes from Around the World:<br>Savor the Flavors</p>
    <svg class="pot-art" width="445" height="470" viewBox="0 0 445 470" role="img" aria-label="Cooking pot illustration with a world map on its side">
      <rect x="0" y="0" width="445" height="470" fill="#f4ecec"/>
    </svg>
    <svg class="event-ribbon" width="390" height="100" viewBox="0 0 390 100">
      <polygon points="0,12 350,40 390,96 30,66" fill="#ffffff" stroke="#5a1e1c" stroke-width="2"/>
      <text x="195" y="62" text-anchor="middle" transform="rotate(6 195 56)" font-family="Montserrat, Arial, sans-serif" font-weight="700" font-size="22" fill="#963a37">PLATE OF PROMISE 2013</text>
    </svg>
  </section>

  <footer class="brand-bar">
    <p class="brand-name">Venture Hollow</p>
  </footer>

  <section class="reply-form">
    <h1 class="welcome">We Look Forward<br>to Seeing You!</h1>
    <div class="tickets">
      <div class="ticket-group">
        <h2>TICKETS</h2>
        <p class="ticket-type">Individual $75/Ticket</p>
        <p>Number of Tickets <span class="blank" style="width:196px"></span></p>
      </div>
      <div class="ticket-group">
        <p class="ticket-type">VH Client $30/Ticket</p>
        <p>Number of Tickets <span class="blank" style="width:196px"></span></p>
      </div>
    </div>
    <div class="contact">
      <p>Name <span class="blank" style="width:485px"></span></p>
      <p>Address <span class="blank" style="width:466px"></span></p>
      <p>Phone <span class="blank" style="width:480px"></span></p>
      <p>Email <span class="blank" style="width:496px"></span></p>
    </div>
    <p class="guests-note">Please list additional names and titles below if responding for more than one person:</p>
    <div class="guest-line" style="top:764px"></div>
    <div class="guest-line" style="top:802px"></div>
  </section>

  <div class="deadline">PLEASE REPLY BY APRIL 19<sup>th</sup></div>
</main>
</body>
</html>
```